Health and Fitness Club requires membership pack

We need a membership pack, like this style (http://www.sheetmakersvault.co.uk/images/A4_pocket_folder_round.jpg) a4 sized.

The front of it should contain our logo, the entire thing should be in the style of our brand/concept. On the inside left side there should be space for copy which we will provide once the design has been selected (approximately 500 words).

At the bottom of the left page inside, should be the following:
telephone icon | zqt icon
pixelbrook logo | chirpnet logo | vuo logo | email logo

with the relevant contact details for our company, underneath this should be our website written so that it occupies the entire width of the page.

our website is www. v o r t a g r i p . ae and our logo is attached

i have included a flyer we recently produced to give you an idea of the creative direction of the brand..

```html
<!DOCTYPE html>
<html lang="en">
<head>
<meta charset="utf-8">
<title>Vortagrip Membership Pack – Inside Spread</title>
<link rel="stylesheet" href="https://fonts.googleapis.com/css2?family=Roboto:wght@400;700&display=swap">
<style>
  :root {
    --bg: #f2f2f2;
    --page-white: #ffffff;
    --page-grey: #ebebeb;
    --brand-red: #a3222b;
    --brand-red-deep: #921d26;
    --ink: #111111;
  }
  html, body {
    margin: 0;
    padding: 0;
    width: 1200px;
    height: 795px;
    overflow: hidden;
    background: var(--bg);
    font-family: "Roboto", Arial, sans-serif;
  }
  .spread {
    position: absolute;
    left: 56px;
    top: 20px;
    width: 1088px;
    height: 755px;
    display: flex;
    box-shadow: 0 2px 8px rgba(0,0,0,0.15);
  }
  .page {
    position: relative;
    width: 544px;
    height: 755px;
    overflow: hidden;
  }
  .page--left { background: var(--page-white); }
  .page--right { background: var(--page-grey); }

  .brand-mark {
    position: absolute;
    left: 0;
    width: 544px;
    top: 268px;
    display: flex;
    align-items: center;
    justify-content: center;
    gap: 8px;
  }
  .brand-mark__dot {
    width: 14px;
    height: 14px;
    border-radius: 50%;
    background: var(--brand-red);
  }
  .brand-mark__name {
    font-weight: 700;
    font-size: 22px;
    letter-spacing: 2px;
    color: var(--ink);
  }

  .contact-band {
    position: absolute;
    left: 0;
    bottom: 0;
    width: 544px;
    height: 80px;
    background: var(--brand-red);
  }
  .contact-icons {
    position: absolute;
    top: 15px;
    left: 0;
    width: 544px;
    display: flex;
    justify-content: center;
    align-items: center;
    gap: 12px;
    color: var(--ink);
  }
  .contact-icons svg { display: block; }
  .contact-icons__label {
    font-weight: 700;
    font-size: 12px;
    line-height: 1;
    color: var(--ink);
  }
  .website {
    position: absolute;
    left: 0;
    top: 40px;
    display: block;
  }
  .website text {
    font-family: "Roboto", Arial, sans-serif;
    font-size: 25px;
    fill: var(--ink);
  }

  .pocket {
    position: absolute;
    left: 0;
    top: 0;
  }
  .pocket__watermark-text {
    font-family: "Roboto", Arial, sans-serif;
    font-weight: 700;
    font-size: 62px;
    fill: var(--brand-red-deep);
  }
</style>
</head>
<body>
  <main class="spread">
    <section class="page page--left" aria-label="Inside left page">
      <div class="brand-mark">
        <span class="brand-mark__dot"></span>
        <span class="brand-mark__name">VORTAGRIP</span>
      </div>

      <footer class="contact-band">
        <div class="contact-icons">
          <svg class="icon-phone" width="14" height="14" viewBox="0 0 24 24" aria-label="Telephone">
            <path d="M6.6 10.8a15.1 15.1 0 0 0 6.6 6.6l2.2-2.2a1 1 0 0 1 1-.25 11.4 11.4 0 0 0 3.6.57 1 1 0 0 1 1 1V20a1 1 0 0 1-1 1A17 17 0 0 1 3 4a1 1 0 0 1 1-1h3.5a1 1 0 0 1 1 1c0 1.25.2 2.45.57 3.6a1 1 0 0 1-.25 1z" fill="currentColor"/>
          </svg>
          <span class="contact-icons__label">zqt</span>
          <span class="contact-icons__label">pixelbrook</span>
          <span class="contact-icons__label">chirpnet</span>
          <span class="contact-icons__label">vuo</span>
          <svg class="icon-email" width="18" height="13" viewBox="0 0 18 13" aria-label="Email">
            <rect x="0.5" y="0.5" width="17" height="12" fill="currentColor"/>
            <path d="M1 1 L9 7.5 L17 1" stroke="#a3222b" stroke-width="1.4" fill="none"/>
          </svg>
        </div>
        <svg class="website" width="544" height="34" viewBox="0 0 544 34">
          <text x="36" y="26" textLength="476" lengthAdjust="spacing">www. v o r t a g r i p . ae</text>
        </svg>
      </footer>
    </section>

    <section class="page page--right" aria-label="Inside right page with pocket">
      <svg class="pocket" width="544" height="755" viewBox="0 0 544 755">
        <defs>
          <clipPath id="pocket-shape">
            <path d="M10,755 C22,580 140,461 322,461 L544,461 L544,755 Z"/>
          </clipPath>
        </defs>
        <path d="M10,755 C22,580 140,461 322,461 L544,461 L544,755 Z" fill="var(--brand-red)" stroke="#c9c9c9" stroke-width="1"/>
        <g clip-path="url(#pocket-shape)">
          <circle cx="330" cy="615" r="165" fill="none" stroke="var(--brand-red-deep)" stroke-width="26"/>
          <text class="pocket__watermark-text" x="330" y="636" text-anchor="middle">VORTAGRIP</text>
        </g>
      </svg>
    </section>
  </main>
</body>
</html>
```